Ringordner
Zielgruppe
Wir sind ein ambulanter Pflegedienst, der im Raum Dessau-Roßlau tätig ist. Wir haben uns mit einer Tagespflege erweitert. Zukünftig ist es geplant, dass wir uns um eine Therapie erweitern. Unsere Zielgruppe sind sämtliche Pflegebedürftige und deren Angehörige. Für die aktuelle Maßnahme sind jedoch die zukünftigen Mitarbeiter im Vordergrund.
Aufgabenstellung
Ich möchte für unsere zukünftigen Mitarbeiter einen A4 Ringordner mit zwei Klammern gestalten. Dieser Ordner wird als Willkomm Mappe für neue Mitarbeiter bei der Aufnahme der Tätigkeit übergeben. Das Design sollte das Hauptlogo des Pflegedienstes enthalten und auf die Tochterfirmen hinweisen. Es sollte modern und frisch wirken und vor allem professionell. Es soll die Mitarbeiter in unserer neuen Firma willkommen heißen.
Dann benötige ich ein zweites Design, dass für die Kunden ist. Es beinhaltet einen Leitfaden, was für die Zusammenarbeit zwischen Pflegedienst und Patient am wichtigsten ist. Dieses Design ist genauso wie beim Mitarbeiter ein A4 Ringordner mit zwei Klammern. Auch dieser Ordner soll diesmal den Patienten bekommen heißen. Hier soll auch das Logo des Pflegedienstes enthalten sein und auch die Tochterfirmen hinweisen.

```html
<!DOCTYPE html>
<html lang="de">
<head>
<meta charset="utf-8">
<title>Ringordner – Willkommen im Team</title>
<link href="https://fonts.googleapis.com/css2?family=Marcellus&family=Raleway:wght@500;600&display=swap" rel="stylesheet">
<style>
  :root {
    --page-bg: #efefef;
    --white: #ffffff;
    --mint-soft: #eef6f4;
    --mint: #d3ebe7;
    --stripe: #b3dedc;
    --ink: #5e5e5e;
    --ink-dark: #3f3f3f;
    --teal: #2a8f8c;
    --orange: #f0a850;
    --photo-light: #c9cfd8;
    --photo-blue: #4d74b8;
    --photo-deep: #2f4f93;
  }
  html, body {
    margin: 0; padding: 0;
    width: 835px; height: 1200px;
    overflow: hidden;
    background: var(--page-bg);
  }
  .cover-spread {
    position: absolute;
    left: 20px; top: 367px;
    width: 795px; height: 466px;
    background: linear-gradient(180deg, var(--white) 0%, var(--white) 45%, var(--mint-soft) 62%, var(--mint) 84%);
    overflow: hidden;
    font-family: "Raleway", sans-serif;
    color: var(--ink);
  }
  .photo-area { position: absolute; left: 436px; top: 0; width: 359px; height: 270px; }
  .brand-title {
    position: absolute; margin: 0;
    font-family: "Raleway", sans-serif; font-weight: 500;
    font-size: 19px; letter-spacing: 0.5px; color: var(--ink);
    text-align: center; width: 300px;
  }
  .back .brand-title { left: 34px; top: 242px; }
  .front .brand-title { left: 466px; top: 243px; }
  .brand-mark {
    position: absolute; display: flex; align-items: center; justify-content: center; gap: 5px;
    font-family: "Raleway", sans-serif; font-weight: 600; color: var(--teal); white-space: nowrap;
  }
  .brand-mark .dot { width: 9px; height: 9px; border-radius: 50%; background: var(--teal); }
  .back .brand-mark.main { left: 134px; top: 196px; width: 100px; font-size: 13px; }
  .front-badge {
    position: absolute; left: 561px; top: 158px; width: 110px; height: 110px;
    border-radius: 50%; background: var(--white);
    display: flex; align-items: center; justify-content: center;
  }
  .front-badge .brand-mark { position: static; font-size: 14px; margin-top: -20px; }
  .partner {
    position: absolute; display: flex; align-items: center; gap: 4px;
    font-family: "Raleway", sans-serif; font-weight: 600; white-space: nowrap;
  }
  .partner .shape { width: 14px; height: 14px; border-radius: 50%; }
  .partner.therapy { color: var(--teal); font-size: 8.5px; }
  .partner.therapy .shape { background: var(--teal); }
  .partner.dayhouse { color: var(--orange); font-size: 8.5px; }
  .partner.dayhouse .shape { background: var(--orange); border-radius: 3px; }
  .partner small { display: block; font-size: 4px; font-weight: 600; letter-spacing: 0.3px; }
  .back .partner.therapy { left: 85px; top: 288px; }
  .back .partner.dayhouse { left: 198px; top: 288px; }
  .tagline {
    position: absolute; left: 34px; top: 330px; width: 300px; margin: 0;
    font-family: "Marcellus", serif; font-weight: 400; font-size: 25px;
    text-align: center; color: var(--ink);
  }
  .headline {
    position: absolute; left: 466px; top: 282px; width: 300px; margin: 0;
    font-family: "Marcellus", serif; font-weight: 400; color: var(--ink);
    text-align: center; line-height: 0.9;
  }
  .headline .big { display: block; font-size: 45px; }
  .headline .small { display: block; font-size: 33px; }
  .footer-band {
    position: absolute; left: 0; top: 391px; width: 795px; height: 60px; background: var(--white);
  }
  .footer-stripe { position: absolute; left: 0; top: 451px; width: 795px; height: 15px; background: var(--stripe); }
  .footer-brand { left: 32px; top: 413px; width: 66px; font-size: 10px; }
  .footer-brand .dot { width: 7px; height: 7px; }
  .footer-text {
    position: absolute; margin: 0;
    font-family: "Raleway", sans-serif; font-weight: 500; font-size: 6.3px; line-height: 10px; color: var(--ink-dark);
  }
  .company { left: 110px; top: 402px; }
  .contact { left: 248px; top: 412px; }
  .footer-band-mark { left: 380px; top: 414px; font-size: 8px; }
  .footer-band-mark .dot { width: 7px; height: 7px; }
  .footer-partners .partner.therapy { left: 502px; top: 414px; font-size: 9.5px; }
  .footer-partners .partner.dayhouse { left: 636px; top: 414px; font-size: 9.5px; }
  .footer-partners .partner .shape { width: 18px; height: 18px; }
</style>
</head>
<body>
  <main class="cover-spread">
    <svg class="photo-area" viewBox="0 0 359 270" width="359" height="270" role="img" aria-label="Foto: Pflegeteam legt die Hände aufeinander">
      <defs>
        <linearGradient id="photoTone" x1="0" y1="0" x2="1" y2="1">
          <stop offset="0" stop-color="#4d74b8"/>
          <stop offset="0.45" stop-color="#c9cfd8"/>
          <stop offset="1" stop-color="#2f4f93"/>
        </linearGradient>
      </defs>
      <path d="M0 0 H359 V186 Q180 218 0 202 Z" fill="url(#photoTone)"/>
    </svg>

    <section class="back">
      <div class="brand-mark main"><span class="dot"></span>Sorvida</div>
      <h2 class="brand-title">TEAM SORVIDA</h2>
      <div class="partner therapy"><span class="shape"></span><span>TEAM SORVIDA<small>THERAPIE</small></span></div>
      <div class="partner dayhouse"><span class="shape"></span><span>Haus Mirabel<small>Ein Tag bei uns ist wie Zuhause</small></span></div>
      <p class="tagline">Wir sind für Sie da!</p>
    </section>

    <section class="front">
      <div class="front-badge"><div class="brand-mark"><span class="dot"></span>Sorvida</div></div>
      <h2 class="brand-title">TEAM SORVIDA</h2>
      <h1 class="headline"><span class="big">Willkomen</span><span class="small">im team</span></h1>
    </section>

    <footer>
      <div class="footer-band"></div>
      <div class="footer-stripe"></div>
      <div class="brand-mark footer-brand"><span class="dot"></span>Sorvida</div>
      <p class="footer-text company">Team Sorvida GmbH<br>Geschäftsführerin: Vera Tannholt<br>Lindenweg 14<br>06000 Auental</p>
      <p class="footer-text contact">030000 / 12 34 56<br>team@sorvida-pflege.de<br>www.sorvida-pflege.de</p>
      <div class="brand-mark footer-band-mark"><span class="dot"></span>Sorvida</div>
      <div class="footer-partners">
        <div class="partner therapy"><span class="shape"></span><span>TEAM SORVIDA<small>THERAPIE</small></span></div>
        <div class="partner dayhouse"><span class="shape"></span><span>Haus Mirabel<small>Ein Tag bei uns ist wie Zuhause</small></span></div>
      </div>
    </footer>
  </main>
</body>
</html>
```